We need a package design for a dietary supplement.

We need a package design for a dietary supplement - throwable tablets - Senegalese acacia fiber with pineapple flavor.
New name BrightOrbit.
Remember the packaging is a white jar, a magenta cap, a sticker, and a cardboard box. We want to change the name to: BrightOrbit (if you have a better idea for the name, just tell me) and refresh the packaging.
Product description:
> Contributes to improving the functioning of the digestive system.
> Boosts metabolism, controls appetite and supports weight loss.
> Helps maintain normal blood sugar levels.
> Regulates cholesterol levels
> 100% natural ingredients in the form of chewable tablets.
It has many beneficial health benefits:
> Cleanses the body of toxins,
> Helps with constipation and bloating,
> Facilitates defecation,
> Regulates cholesterol levels (by eliminating bile acids from the intestine),
> Adds energy,
> Improves metabolism,
> reduces appetite,
> Improves the work of the digestive system,
> It can help to get rid of the unpleasant smell from the mouth,
> Improves well-being,
> Regular intake can lead to weight loss,
> It works gently and does not cause side effects,
> Delays the aging process,
> Improves the appearance of the skin
This all-natural dietary supplement supports heart health, helps maintain blood sugar levels, soothes irritable bowel syndrome, and improves overall gut health.

100% natural, vegan product, no added sugars, no added salt. It has only 2 ingredients: Cenegal acacia and pineapple juice.

We are changing the name and packaging for our product called KestroNuma. Photos attached, packaging grid attached, samples of our other packaging attached.
*Packaging in Dutch

Target Market(s)

Netherlands

Industry/Entity Type

dietary supplements

Colors

Designer to choose colors to be used in the design.

Requirements
Must have
• Modern and inspire patient confidence.
Nice to have
• Good, natural, healthy
Should not have
• It should not clearly indicate that it has a slimming effect, as in the kestronuma project

```html
<!DOCTYPE html>
<html lang="en">
<head>
<meta charset="utf-8">
<title>BrightOrbit – Label</title>
<link href="https://fonts.googleapis.com/css2?family=Montserrat:wght@300;400;500;700;800&family=Josefin+Sans:wght@400&display=swap" rel="stylesheet">
<style>
  :root {
    --canvas: #ffffff;
    --black: #121212;
    --black-sheen: #3a3a3a;
    --green-light: #5a7a44;
    --green-mid: #3b5424;
    --green-dark: #253a16;
    --green-deep: #1c2e10;
    --logo-green: #6f9a48;
    --subtitle-green: #3d5529;
    --white: #ffffff;
    --ink: #0d130a;
  }
  * { margin: 0; padding: 0; box-sizing: border-box; }
  html, body {
    width: 1200px; height: 1200px; overflow: hidden;
    background: var(--canvas);
  }
  .canvas {
    position: relative; width: 1200px; height: 1200px;
  }
  .label {
    position: absolute; left: 120px; top: 62px;
    width: 960px; height: 1075px; overflow: hidden;
    font-family: "Montserrat", sans-serif;
    color: var(--white);
  }
  .label-top {
    position: absolute; left: 0; top: 0; width: 100%; height: 526px;
    background:
      radial-gradient(ellipse 520px 360px at 120px 80px, var(--black-sheen) 0%, rgba(40,40,40,0) 70%),
      var(--black);
  }
  .label-band-light {
    position: absolute; left: 0; top: 526px; width: 100%; height: 274px;
    background: linear-gradient(90deg, var(--green-light) 0%, var(--green-mid) 40%, var(--green-mid) 70%, var(--green-light) 100%);
  }
  .label-band-dark {
    position: absolute; left: 0; top: 800px; width: 100%; height: 275px;
    background: linear-gradient(90deg, var(--green-mid) 0%, var(--green-dark) 50%, var(--green-deep) 100%);
  }
  .brand {
    position: absolute; left: 78px; top: 128px;
    display: flex; align-items: center; gap: 14px;
    font-weight: 500; font-size: 40px; letter-spacing: 1px;
    color: var(--logo-green);
  }
  .brand-dot {
    width: 18px; height: 18px; border-radius: 50%;
    background: var(--logo-green);
  }
  .count {
    position: absolute; left: 672px; top: 132px;
    font-weight: 300; font-size: 34px; letter-spacing: 1px;
  }
  .product-name {
    position: absolute; left: 70px; top: 290px;
  }
  .product-name text { font-family: "Montserrat", sans-serif; fill: var(--white); }
  .product-name .light { font-weight: 300; }
  .product-name .bold { font-weight: 700; }
  .subtitle {
    position: absolute; left: 72px; top: 426px;
    font-weight: 400; font-size: 32px; letter-spacing: 10.6px;
    color: var(--subtitle-green);
  }
  .claims {
    position: absolute; left: 56px; top: 598px; width: 760px;
    font-family: "Josefin Sans", sans-serif;
    font-size: 26px; line-height: 34px; letter-spacing: 2.4px;
    text-transform: uppercase;
  }
  .category {
    position: absolute; left: 64px; top: 852px;
    font-family: "Josefin Sans", sans-serif;
    font-size: 28px; letter-spacing: 1.6px;
  }
  .rule {
    position: absolute; left: 53px; top: 936px;
    width: 460px; height: 3px; background: var(--ink);
  }
  .feature {
    position: absolute; top: 982px;
    font-family: "Josefin Sans", sans-serif;
    font-size: 28px; letter-spacing: 0.6px;
  }
  .feature-sugar { left: 58px; }
  .feature-vegan { left: 560px; }
  .feature-dot {
    position: absolute; left: 501px; top: 991px;
    width: 16px; height: 16px; border-radius: 50%; background: var(--ink);
  }
  .seal { position: absolute; left: 745px; top: 702px; }
</style>
</head>
<body>
<div class="canvas">
  <div class="label">
    <div class="label-top"></div>
    <div class="label-band-light"></div>
    <div class="label-band-dark"></div>

    <div class="brand"><span class="brand-dot"></span>NOORDVELD</div>
    <div class="count">100 CAPS</div>

    <svg class="product-name" width="820" height="130" viewBox="0 0 820 130">
      <text x="0" y="118" font-size="146" textLength="800" lengthAdjust="spacingAndGlyphs"><tspan class="light">BRIGHT</tspan><tspan class="bold">ORBIT</tspan></text>
    </svg>

    <div class="subtitle">SENEGALESE ACACIA FIBER</div>

    <p class="claims">All-natural dietary supplement supports heart health, helps maintain blood sugar levels, soothes irritable bowel syndrome, and improves overall gut health.</p>

    <div class="category">DIETARY SUPPLEMENT</div>
    <div class="rule"></div>
    <div class="feature feature-sugar">NO ADDED SUGAR OR SALT</div>
    <div class="feature-dot"></div>
    <div class="feature feature-vegan">VEGAN PRODUCT</div>

    <svg class="seal" width="184" height="184" viewBox="0 0 184 184" role="img" aria-label="Natural product seal">
      <circle cx="92" cy="92" r="88" fill="var(--green-dark)" opacity="0.55"/>
      <circle cx="92" cy="92" r="82" fill="none" stroke="var(--ink)" stroke-width="3"/>
      <circle cx="92" cy="92" r="52" fill="none" stroke="var(--ink)" stroke-width="3"/>
    </svg>
  </div>
</div>
</body>
</html>
```